Financial & Tax Strategies

need to get a word press site with existing domains and condense existing content on existing site, make new site dynamic, need mobile too......need to take info from my quorvia website and get modern, relevant site, less verbose on first page, way more things to click and engage people. Would like it to look like this , but with my color scheme and not quite as busy looking. I like much of the content on my tabs. Want maximize by seo capabilities on their as well. The number one thing I can say is to go to my existing website and get content, logo, etc there … www.pinegatelarkgroup.com .

Target Market(s)

Those 40 -65, business owners for at least 5 years. Higher net worth.

Number of Pages Required

5+ page

Font styles to use
Sans Serif

Colors
f04a50
e4daeb
ffffff

Requirements
Must have
• seo maximized, lots of places to click on to contact us, calls to action, relevant, conservative, want it to look like this and have the function as well.....slight variation on messaging, but like the simplicity on first view. https://www.dorrickvale.com/
Nice to have
• Some area along right side where videos we do will be.
Should not have
• feel too busy, but still have lots of opportunities to engage.

```html
<!DOCTYPE html>
<html lang="en">
<head>
<meta charset="utf-8">
<title>Pinegate Lark Group — Sensible Financial Solutions</title>
<link rel="stylesheet" href="https://fonts.googleapis.com/css2?family=Roboto:wght@300;400;500;700&display=swap">
<style>
:root{
  --red:#e8222a;
  --ink:#222222;
  --text:#555555;
  --muted:#888888;
  --line:#e2e2e2;
  --band:#efefef;
  --page:#f4f4f4;
  --white:#ffffff;
  --footer:#2b2b2b;
  --footer-text:#d8d8d8;
}
*{box-sizing:border-box;margin:0;padding:0}
html,body{width:1200px;height:3629px;overflow:hidden}
body{position:relative;font-family:'Roboto',Arial,sans-serif;color:var(--text);background:var(--white)}
.abs{position:absolute}
.btn{display:inline-block;background:var(--red);color:var(--white);font-weight:700;font-size:14px;border-radius:20px;padding:10px 28px;text-decoration:none}
.section-title{position:absolute;left:0;width:1200px;text-align:center;font-size:34px;font-weight:400;color:var(--ink)}

/* header */
.site-header{top:0;left:0;width:1200px;height:97px;background:var(--white)}
.menu-icon{left:80px;top:34px}
.brand{left:490px;top:24px;display:flex;align-items:center;gap:12px}
.brand-mark{width:44px;height:44px;border-radius:50%;background:#8a8a8a}
.brand-name{font-size:22px;font-weight:500;color:var(--ink);line-height:1.05}
.call-now{right:80px;top:30px;display:flex;align-items:center;gap:10px}
.call-now .label{font-size:12px;color:var(--red);font-weight:500;line-height:1.2}
.call-now .num{font-size:13px;color:var(--ink)}

/* hero */
.hero{top:97px;left:0;width:1200px;height:540px;background:linear-gradient(180deg,#b9c8cc 0%,#8fa28f 28%,#6f9a48 55%,#5c8a32 100%)}
.hero-box{left:352px;top:188px;width:496px;height:222px;border:1px solid rgba(255,255,255,.55);background:rgba(40,50,40,.28);text-align:center;padding-top:48px}
.hero-box h1{font-size:35px;font-weight:400;color:var(--white)}
.hero-box p{font-size:16px;color:#eeeeee;margin:8px auto 20px;width:380px;line-height:1.3}
.arrow{top:350px}
.hero-dots{left:580px;top:600px;display:flex;gap:8px}
.hero-dots span{width:9px;height:9px;border-radius:50%;background:rgba(255,255,255,.6)}
.hero-dots span.on{background:var(--white)}

/* about */
.divider{left:545px;display:flex;align-items:center;gap:8px}
.divider i{width:40px;height:2px;background:var(--red)}
.divider b{width:16px;height:16px;border:3px solid #888;border-radius:50%}
.about-text{left:200px;top:786px;width:800px;text-align:center;font-size:13.5px;line-height:1.5}

/* services */
.card{top:1065px;width:240px;height:218px;border-radius:22px;background:var(--white);box-shadow:0 2px 14px rgba(0,0,0,.07);text-align:center;padding-top:60px}
.card.feature{background:var(--red)}
.card h3{font-size:16px;font-weight:400;color:var(--ink);line-height:1.3;margin-top:16px}
.card.feature h3{color:var(--white)}

/* graphs band */
.graphs{top:1387px;left:0;width:1200px;height:513px;background:var(--band)}
.graphs h2{position:absolute;left:80px;top:100px;font-size:32px;font-weight:400;color:var(--ink);line-height:1.2;width:460px}
.graphs p{position:absolute;left:80px;top:210px;width:440px;font-size:14px;line-height:1.5}
.graphs .btn{position:absolute;left:80px;top:338px}
.screen{position:absolute;left:590px;top:68px;width:560px;height:380px;background:#1d1d1d;border-radius:14px;padding:14px}
.screen-base{position:absolute;left:520px;top:448px;width:680px;height:18px;background:#c9c9c9;border-radius:0 0 30px 30px}

/* blogs */
.blog{top:2040px;width:345px;height:380px;background:var(--white);box-shadow:0 2px 12px rgba(0,0,0,.08);padding:12px}
.blog .thumb{height:210px}
.blog .meta{font-size:12px;color:var(--muted);display:flex;justify-content:space-between;margin:10px 4px 4px}
.blog h4{font-size:14px;color:var(--ink);font-weight:500;margin:8px 4px 6px}
.blog p{font-size:13px;line-height:1.4;margin:0 4px}
.blog .more{display:inline-block;font-size:12px;color:var(--ink);border-bottom:1px solid var(--red);margin:12px 4px 0}

/* testimonials */
.quote{top:2613px;width:238px;height:340px;background:var(--white);border-radius:14px;box-shadow:0 2px 14px rgba(0,0,0,.08);text-align:center;padding:20px 14px}
.avatar{width:90px;height:90px;border-radius:50%;margin:0 auto 10px;background:linear-gradient(180deg,#c9ced4,#8e969e)}
.quote h5{font-size:16px;color:var(--ink);font-weight:500}
.quote .role{font-size:12.5px;color:var(--red);line-height:1.3;margin:2px 0 8px}
.quote p{font-size:12.5px;line-height:1.4}
.t-dots{left:580px;top:2972px;display:flex;gap:8px}
.t-dots span{width:8px;height:8px;border-radius:50%;background:#f3a3a6}
.t-dots span.on{background:var(--red)}

/* contact strip */
.email-input{left:302px;top:3082px;width:440px;height:36px;border:1px solid var(--line);border-radius:18px 0 0 18px;font-size:12px;color:var(--muted);padding:10px 20px}
.email-submit{left:738px;top:3082px;width:160px;height:36px;background:var(--red);color:var(--white);border-radius:18px;font-size:14px;font-weight:700;text-align:center;line-height:36px}
.call-us{left:0;width:1200px;top:3148px;display:flex;justify-content:center;align-items:center;gap:18px;font-size:30px;font-weight:700;color:var(--ink)}
.call-us .num{color:var(--red)}

/* footer */
.site-footer{top:3247px;left:0;width:1200px;height:311px;background:var(--footer);color:var(--footer-text);font-size:13.5px}
.f-col{position:absolute;top:60px}
.f-col h6{font-size:15px;font-weight:500;color:var(--white);border-bottom:2px solid var(--red);display:inline-block;padding-bottom:4px;margin-bottom:12px}
.f-col ul{list-style:none;line-height:1.75}
.f-col ul li::before{content:"•";margin-right:8px}
.f-brand{display:flex;align-items:center;gap:10px;margin-bottom:12px}
.f-brand .dot{width:38px;height:38px;border-radius:50%;background:var(--white)}
.f-brand span{font-size:21px;color:var(--white);font-weight:500;line-height:1.05}
.addr div{display:flex;gap:10px;line-height:1.55;margin-bottom:4px}
.field{background:#444;height:28px;font-size:12px;color:var(--white);padding:6px 10px}
.copyright{top:3558px;left:0;width:1200px;height:71px;background:var(--white);font-size:12px;color:var(--ink)}
.social{position:absolute;right:80px;top:24px;display:flex;gap:10px}
.social span{width:22px;height:22px;border-radius:50%;background:var(--red)}
</style>
</head>
<body>

<header class="site-header abs">
  <svg class="menu-icon abs" width="24" height="18" viewBox="0 0 24 18"><rect width="24" height="2.5" fill="#333"/><rect y="7.5" width="24" height="2.5" fill="#333"/><rect y="15" width="24" height="2.5" fill="#333"/></svg>
  <div class="brand abs"><span class="brand-mark"></span><span class="brand-name">Pinegate Lark<br>Group</span></div>
  <div class="call-now abs">
    <svg width="30" height="30" viewBox="0 0 30 30"><circle cx="15" cy="15" r="15" fill="#e8222a"/><path d="M10 8c1-1 2 0 3 2s0 2-1 3c1 2 3 4 5 5 1-1 1-2 3-1s3 2 2 3c-1 2-3 3-6 1-3-2-5-4-7-7-1-3 0-5 1-6z" fill="#fff"/></svg>
    <div><div class="label">Call us Now</div><div class="num">555.210.4470</div></div>
  </div>
</header>

<section class="hero abs" role="img" aria-label="Alpine valley with green meadows, village and mountains">
  <svg class="arrow abs" style="left:40px" width="16" height="28" viewBox="0 0 16 28"><path d="M14 2L2 14l12 12" stroke="#fff" stroke-width="3" fill="none"/></svg>
  <svg class="arrow abs" style="right:40px" width="16" height="28" viewBox="0 0 16 28"><path d="M2 2l12 12L2 26" stroke="#fff" stroke-width="3" fill="none"/></svg>
  <div class="hero-box abs">
    <h1>Sensible Financial Solutions</h1>
    <p>Want predictable cash flow when you retire? We do what financial advisors &amp; accountants don't.</p>
    <a class="btn">Superior Game Plan</a>
  </div>
  <div class="hero-dots abs"><span></span><span class="on"></span><span></span></div>
</section>

<h2 class="section-title" style="top:702px">About us</h2>
<div class="divider abs" style="top:752px"><i></i><b></b><i></i></div>
<p class="about-text abs">As retirement inches closer, have you ever wondered if there were a company that could secure better returns than CD's, yet still be able to access your money inexpensively and as importantly, avoid the years it takes for your portfolio to recover from the big and routine crashes like in '87, '93, 2001 and 2008? What if Pinegate Lark Group could provide this peace of mind AND not charge you those seemingly small (1-3%) portfolio devastating fees? Your financial advisor can never promise that you will get "X" per month on date "X"....why? We can answer that and we can guarantee both.</p>
<a class="btn abs" style="left:485px;top:896px">Too good to be true? Try us</a>

<h2 class="section-title" style="top:990px">The Only Business Like Our Business</h2>

<div class="card abs" style="left:80px">
  <svg width="44" height="44" viewBox="0 0 44 44"><rect x="6" y="24" width="6" height="16" fill="#e8222a"/><rect x="16" y="16" width="6" height="24" fill="#e8222a"/><rect x="26" y="20" width="6" height="20" fill="#e8222a"/><path d="M4 20l12-10 8 6 14-12" stroke="#e8222a" stroke-width="2.5" fill="none"/><rect x="2" y="40" width="40" height="2" fill="#e8222a"/></svg>
  <h3>Portfolio Crash<br>Protection</h3>
</div>
<div class="card feature abs" style="left:347px">
  <svg width="44" height="44" viewBox="0 0 44 44"><path d="M12 4v20h20M14 24l-6 14M30 24l6 14M4 38c10 4 26 4 36 0" stroke="#fff" stroke-width="3" fill="none"/><circle cx="22" cy="10" r="5" fill="none" stroke="#fff" stroke-width="3"/></svg>
  <h3>Fees Kill Retirements<br>Planning</h3>
</div>
<div class="card abs" style="left:614px">
  <svg width="48" height="44" viewBox="0 0 48 44"><rect x="4" y="4" width="40" height="22" fill="#e8222a"/><rect x="8" y="26" width="32" height="16" fill="none" stroke="#e8222a" stroke-width="2.5"/><rect x="14" y="10" width="20" height="8" fill="#fff"/><rect x="14" y="32" width="20" height="2" fill="#e8222a"/></svg>
  <h3>Here's How,Business<br>Owner &amp;<br>Executive Advantage</h3>
</div>
<div class="card abs" style="left:881px">
  <svg width="40" height="48" viewBox="0 0 40 48"><circle cx="20" cy="12" r="9" fill="#e8222a"/><path d="M20 21v12M8 30c4-4 8-2 12 3 4-5 8-7 12-3" stroke="#e8222a" stroke-width="2.5" fill="none"/><path d="M10 36h20l-3 10H13z" fill="#e8222a"/></svg>
  <h3>401k &amp; Mutual<br>Fund Illusion</h3>
</div>

<section class="graphs abs">
  <h2>Graphs can speak a thousand words</h2>
  <p>Ever wonder how much of your portfolio is the money you put into your 401k, IRA or Mutual Fund and how much those accounts have netted you over the last 10, 20, 30 years plus? Fees, crashes and financial advisors have not and will not educate you on this. We'll get you up to speed on your money and your financial future.</p>
  <a class="btn">Read More</a>
  <div class="screen">
    <svg width="532" height="352" viewBox="0 0 532 352" role="img" aria-label="Line chart comparing annual market change with a floor-and-cap growth strategy">
      <rect width="532" height="352" fill="#fff"/>
      <text x="266" y="18" font-size="11" font-weight="700" text-anchor="middle" fill="#222" font-family="Roboto,sans-serif">Historical Comparison: Broad Market Index vs. 0% Floor and 10% Cap Growth</text>
      <g stroke="#ddd" stroke-width="1">
        <line x1="50" y1="50" x2="490" y2="50"/><line x1="50" y1="95" x2="490" y2="95"/><line x1="50" y1="140" x2="490" y2="140"/><line x1="50" y1="185" x2="490" y2="185"/><line x1="50" y1="230" x2="490" y2="230"/><line x1="50" y1="275" x2="490" y2="275"/><line x1="50" y1="320" x2="490" y2="320"/>
      </g>
      <g font-size="10" fill="#333" font-family="Roboto,sans-serif" text-anchor="end">
        <text x="44" y="54">120%</text><text x="44" y="99">80%</text><text x="44" y="144">40%</text><text x="44" y="189">0%</text><text x="44" y="234">-40%</text><text x="44" y="279">-80%</text><text x="44" y="324">-120%</text>
      </g>
      <polyline points="60,185 100,185 140,170 180,160 220,150 260,140 300,135 340,135 380,112 420,100 460,95" fill="none" stroke="#2b6ea8" stroke-width="3"/>
      <polyline points="60,185 100,205 140,230 180,210 220,200 260,195 300,180 340,230 380,205 420,195 460,190" fill="none" stroke="#c4262e" stroke-width="3"/>
      <g fill="#2b6ea8"><circle cx="60" cy="185" r="3.5"/><circle cx="180" cy="160" r="3.5"/><circle cx="300" cy="135" r="3.5"/><circle cx="460" cy="95" r="3.5"/></g>
      <g fill="#c4262e"><circle cx="140" cy="230" r="3.5"/><circle cx="260" cy="195" r="3.5"/><circle cx="340" cy="230" r="3.5"/><circle cx="460" cy="190" r="3.5"/></g>
      <g font-size="10" fill="#333" font-family="Roboto,sans-serif">
        <circle cx="140" cy="340" r="4" fill="#c4262e"/><text x="148" y="344">Annual Change in Market</text>
        <circle cx="300" cy="340" r="4" fill="#2b6ea8"/><text x="308" y="344">Annual Change with Floor and Cap</text>
      </g>
    </svg>
  </div>
  <div class="screen-base"></div>
</section>

<h2 class="section-title" style="top:1970px">Blogs, Videos &amp; Radio</h2>

<article class="blog abs" style="left:65px">
  <div class="thumb" role="img" aria-label="Businessman celebrating under falling banknotes" style="background:linear-gradient(180deg,#c9c9c9,#8d8d8d)"></div>
  <h4 style="margin-top:18px">Money Blog</h4>
  <p>Lorem Ipsum is simply dummy the printing and typesetting industry. Lorem Ipsum has been the in the standard dummy.</p>
  <span class="more">Continue...</span>
</article>
<article class="blog abs" style="left:430px">
  <div class="thumb" role="img" aria-label="Portrait of a smiling advisor in a suit" style="background:linear-gradient(180deg,#b8c6d2,#6d8096)"></div>
  <div class="meta"><span></span><span>♡ 12</span></div>
  <h4>PLG Videos</h4>
  <p>Lorem Ipsum is simply dummy the printing and typesetting industry. Lorem Ipsum has been the in the standard dummy.</p>
  <span class="more">Continue...</span>
</article>
<article class="blog abs" style="left:795px">
  <div class="thumb" style="background:#fafafa;display:flex;align-items:center;justify-content:center"><span style="font-size:34px;font-weight:700;color:#222">StreamWave Radio</span></div>
  <div class="meta"><span>▦ Mar 21, 2019</span><span>◯ 20 &nbsp; ♡ 12</span></div>
  <h4>StreamWave Radio</h4>
  <p>Catch us on StreamWave Radio's Lena Marsh Show (Cash Flow Carl &amp; Steady Sam)</p>
  <span class="more">Continue...</span>
</article>

<a class="btn abs" style="left:495px;top:2462px">10 Reasons 401ks Fail</a>

<h2 class="section-title" style="top:2538px">Testimonials</h2>

<div class="quote abs" style="left:180px">
  <div class="avatar" role="img" aria-label="Client portrait"></div>
  <h5>Tom Wexler</h5>
  <div class="role">National Business Council<br>Turnaround CEO of the Year</div>
  <p>"I'm a CFO by trade, PLG has strategies for families, executive &amp; business owners that accountants and financial advisors don't have. Highest recommendation</p>
</div>
<div class="quote abs" style="left:448px">
  <div class="avatar" role="img" aria-label="Client portrait"></div>
  <h5>Jack Jordan</h5>
  <div class="role">Probate Attorney</div>
  <p>As an attorney, my job is to weigh risk. As an investor, weighing risk and reward is even more important. As someone retiring in next 15 years, I wanted to eliminate the risks of a stock market crash. PLG does this better than any other company.</p>
</div>
<div class="quote abs" style="left:716px">
  <div class="avatar" role="img" aria-label="Client portrait"></div>
  <h5>Glen Hartley</h5>
  <div class="role">Doctor</div>
  <p>Being a doctor requires attention to detail. Pinegate Lark Group helped navigate and educate me on exactly how to decipher my portfolio statement. I would have changed 10 years ago if I would have known what I know now about money. Call them; you'll be happy you did</p>
</div>
<div class="t-dots abs"><span class="on"></span><span></span><span></span></div>

<h2 class="section-title" style="top:3028px;font-size:26px">Shoot us a quick email here</h2>
<div class="email-input abs">Email Here</div>
<div class="email-submit abs">Submit</div>

<div class="call-us abs">
  <span>CALL US</span>
  <svg width="56" height="56" viewBox="0 0 30 30"><circle cx="15" cy="15" r="15" fill="#e8222a"/><path d="M10 8c1-1 2 0 3 2s0 2-1 3c1 2 3 4 5 5 1-1 1-2 3-1s3 2 2 3c-1 2-3 3-6 1-3-2-5-4-7-7-1-3 0-5 1-6z" fill="#fff"/></svg>
  <span class="num">555.210.4470</span>
</div>

<footer class="site-footer abs">
  <div class="f-col" style="left:80px;width:280px;top:62px">
    <div class="f-brand"><span class="dot"></span><span>Pinegate Lark<br>Group</span></div>
    <p style="line-height:1.55">Pinegate Lark Group Bringing sensibility, predictability and peace of mind in retirement. We will do things for your financial lives accountants and financial advisors won't and can't.</p>
  </div>
  <div class="f-col" style="left:404px">
    <h6>Quick Link</h6>
    <ul><li>Home</li><li>About us</li><li>Services</li><li>Blogs</li><li>Testimonials</li><li>Contact us</li></ul>
  </div>
  <div class="f-col addr" style="left:573px;width:220px">
    <h6>Address</h6>
    <div><span>⌖</span><span>2187 Alder Crest Road,<br>Fairmont,<br>CA 95310</span></div>
    <div><span>✆</span><span>555.210.4470</span></div>
    <div><span>✉</span><span>Sales@PinegateLark.com</span></div>
  </div>
  <div class="f-col" style="left:828px;width:292px">
    <h6>Contact us</h6>
    <div style="display:flex;gap:6px">
      <div class="field" style="flex:1">Name</div><div class="field" style="flex:1">Email</div><div class="field" style="flex:1">Phone</div>
    </div>
    <div class="field" style="height:70px;margin-top:6px">Message</div>
    <a class="btn" style="margin-top:12px;font-size:13px;padding:8px 22px">Baby Boomer Edition</a>
  </div>
</footer>

<div class="copyright abs">
  <p style="position:absolute;left:80px;top:28px">CopyRight © 2019 Pinegate Lark Group. All Right Reserve</p>
  <div class="social"><span></span><span></span><span></span><span></span><span></span></div>
</div>

</body>
</html>
```